Chomp-iZ Salsa Website

Needing a website to promote and sell our salsa line.

Each tab at the top of our home page will be need to be clickable taking you to another page. Other pages besides the home page include: about us, recipes, buy now, events, contact us.
Updates

Our project brief has been updated to reflect more details.

Coding

Coded - Design and coding required

Number of Pages Required

5+ page

Requirements
Must have
• Follow us on Friendbook and Instagram.

Buy now page will need to have option to add products to shopping chart. We have a PayLo account that will need to linked to shopping chart for payments.

```html
<!DOCTYPE html>
<html lang="en">
<head>
<meta charset="utf-8">
<title>Chomp-iZ Salsa</title>
<link href="https://fonts.googleapis.com/css2?family=Poppins:wght@500;600;700;800&family=IBM+Plex+Sans:wght@400;500&display=swap" rel="stylesheet">
<style>
:root{
  --black:#000;
  --ink:#111;
  --text:#333;
  --muted:#555;
  --yellow:#f5b416;
  --red:#d8262b;
  --blue:#1f6fc9;
  --white:#fff;
  --paper:#efefef;
  --line:#d8d8d8;
}
*{box-sizing:border-box;margin:0;padding:0}
html,body{width:1200px;height:3547px;overflow:hidden}
body{font-family:"IBM Plex Sans",Arial,sans-serif;color:var(--text);background:var(--white);position:relative}
.abs{position:absolute}
section,header,footer{position:absolute;left:0;width:1200px}
.heading{font-family:"Poppins",Arial,sans-serif;font-weight:700;color:var(--ink)}
.btn{position:absolute;display:flex;align-items:center;justify-content:center;background:var(--yellow);color:var(--ink);font-family:"Poppins",Arial,sans-serif;font-weight:700;text-decoration:none}
.rule{position:absolute;height:3px;background:var(--yellow)}

/* header */
.site-header{top:0;height:117px;background:var(--black);color:var(--white)}
.brand{position:absolute;left:134px;top:44px;font-family:"Poppins",sans-serif;font-weight:700;font-size:22px;line-height:1;color:var(--white)}
.contact-chip{position:absolute;top:24px;display:flex;align-items:center;gap:12px}
.contact-chip .label{font-size:9px;letter-spacing:.5px;text-transform:uppercase}
.contact-chip .value{font-size:15px}
.contact-chip .value.big{font-size:18px}
.cart{position:absolute;left:989px;top:32px;display:flex;align-items:center;gap:6px;font-size:9px}
.cart .count{position:absolute;left:65px;top:-9px;width:16px;height:16px;border-radius:50%;background:var(--yellow);color:var(--ink);font-size:10px;display:flex;align-items:center;justify-content:center;font-weight:600}
.main-nav a{position:absolute;top:80px;font-size:14px;color:var(--white);text-decoration:none;letter-spacing:.3px}
.main-nav a.current{color:var(--yellow);text-decoration:underline;text-underline-offset:4px}

/* hero */
.hero{top:117px;height:581px;background:linear-gradient(100deg,#3b3836 0%,#2a2625 40%,#3a302b 70%,#5a4a3e 100%)}
.hero-jar{left:179px;top:69px;width:303px;height:427px;border-radius:40px 40px 30px 30px;background:linear-gradient(180deg,#1c1c1c 0 18%,#a8201c 18% 40%,#1f1f1f 40% 80%,#a8201c 80%)}
.hero-title{left:621px;top:111px;font-family:"Poppins",sans-serif;font-weight:800;font-size:50px;line-height:64px;color:var(--white)}
.hero-sub{left:624px;top:253px;width:412px;font-size:23px;line-height:34px;color:var(--white)}
.hero .btn{left:627px;top:353px;width:142px;height:51px;font-size:19px}

/* welcome */
.welcome{top:698px;height:589px}
.welcome .kicker{left:131px;top:92px;font-family:"Poppins",sans-serif;font-weight:500;font-size:18px;color:var(--ink)}
.welcome h1{position:absolute;left:131px;top:114px;font-size:33px}
.welcome .rule{left:131px;top:176px;width:106px}
.welcome .lead{left:132px;top:207px;width:330px;font-family:"Poppins",sans-serif;font-weight:500;font-size:16.5px;line-height:24px;color:var(--ink)}
.welcome .body{left:132px;top:279px;width:305px;font-size:13.5px;line-height:19.3px;color:var(--text)}
.welcome .btn{left:132px;top:466px;width:112px;height:39px;font-size:14px;color:var(--white)}
.welcome-photo{left:507px;top:85px;width:562px;height:445px;background:linear-gradient(180deg,#9b958d 0%,#7f7a73 45%,#e9e2c7 75%,#3a3a3a 100%)}
.deco-hat{left:471px;top:39px;width:163px;height:60px;border-radius:50%;background:var(--red)}

/* flavours */
.flavours{top:1287px;height:683px;background:linear-gradient(180deg,#7a4436 0%,#5b3128 30%,#3a2620 60%,#2e3236 100%)}
.flavours-photo{left:150px;top:170px;width:900px;height:390px;border-radius:30px;background:linear-gradient(180deg,#161616 0 8%,#6b3a22 8% 38%,#1a1a1a 38% 80%,#6b3a22 80%)}
.flavours h2{position:absolute;left:0;width:1205px;top:36px;text-align:center;font-size:30px;color:var(--white)}
.flavours .rule{left:568px;top:87px;width:74px}
.flavour-name{top:134px;width:200px;margin-left:-100px;text-align:center;font-family:"Poppins",sans-serif;font-weight:700;font-size:20px;color:var(--white)}
.flavours .btn{left:540px;top:602px;width:119px;height:44px;font-size:16px}
.deco-chili{width:135px;height:56px;border-radius:60% 40% 60% 40%;background:var(--red)}

/* events */
.events{top:1970px;height:635px}
.events h2{position:absolute;left:0;width:1205px;top:50px;text-align:center;font-size:30px}
.events .rule{left:568px;top:103px;width:73px}
.event-card{position:absolute;top:150px;width:301px;height:416px;border:1px solid var(--line);background:var(--white)}
.event-card .photo{height:197px;background:linear-gradient(180deg,#4b3a32,#7a6a5e)}
.event-card .date{position:absolute;left:27px;top:222px;height:22px;padding:0 7px;background:var(--blue);color:var(--white);font-family:"Poppins",sans-serif;font-weight:600;font-size:11.5px;display:flex;align-items:center}
.event-card h3{position:absolute;left:27px;top:254px;font-family:"Poppins",sans-serif;font-weight:600;font-size:18px;color:var(--ink)}
.event-card p{position:absolute;left:27px;top:286px;width:260px;font-size:15.5px;line-height:22.5px;color:var(--muted)}
.event-card .btn{left:27px;top:367px;width:83px;height:28px;font-size:10.5px;color:var(--white)}

/* product */
.product{top:2605px;height:585px;background:var(--paper)}
.product h2{position:absolute;left:0;width:1205px;top:42px;text-align:center;font-size:30px}
.product .rule{left:564px;top:102px;width:78px}
.product-card{left:132px;top:150px;width:936px;height:372px;background:var(--white)}
.product-jar{left:61px;top:42px;width:207px;height:310px;border-radius:30px 30px 24px 24px;background:linear-gradient(180deg,#1c1c1c 0 22%,#b0231d 22% 42%,#1f1f1f 42% 80%,#b0231d 80%)}
.product-divider{left:331px;top:48px;width:1px;height:316px;background:var(--line)}
.product-card h3{position:absolute;left:396px;top:44px;font-family:"Poppins",sans-serif;font-weight:600;font-size:30px;color:var(--ink)}
.product-card .desc{left:397px;top:90px;width:480px;font-size:12.5px;line-height:16px;color:var(--text)}
.product-card .price{left:397px;top:136px;font-size:23px;color:var(--ink)}
.features{left:397px;top:186px;width:440px;display:grid;grid-template-columns:205px 205px;row-gap:8px;list-style:none}
.features li{display:flex;align-items:center;gap:8px;font-size:12.5px;line-height:16px;color:var(--text)}
.product-card .btn{left:398px;top:280px;width:113px;height:40px;font-size:16px}

/* footer */
.site-footer{top:3190px;height:357px;background:var(--black);color:var(--white)}
.footer-brand{left:131px;top:118px;font-family:"Poppins",sans-serif;font-weight:700;font-size:34px;line-height:1;color:var(--white)}
.footer-title{top:60px;font-family:"Poppins",sans-serif;font-weight:700;font-size:12.5px;letter-spacing:.4px}
.footer-menu{left:479px;top:97px;list-style:none}
.footer-menu li{font-size:12.5px;line-height:20px}
.footer-item{display:flex;align-items:flex-start;gap:10px;font-size:12px;line-height:15px}
.footer-item .dot{flex:none;width:22px;height:22px;border-radius:50%;background:var(--white);display:flex;align-items:center;justify-content:center}
.footer-line{left:131px;top:278px;width:939px;height:1px;background:#333}
.copyright{left:0;width:1195px;top:320px;text-align:center;font-size:10px}
</style>
</head>
<body>

<header class="site-header">
  <div class="brand">Chomp-iZ Salsa</div>

  <div class="contact-chip" style="left:551px">
    <svg width="22" height="16" viewBox="0 0 22 16" fill="none" stroke="#fff" stroke-width="1.5"><rect x="1" y="1" width="20" height="14" rx="1"/><path d="M1 1l10 8 10-8"/></svg>
    <div><div class="label">Email us</div><div class="value">info@ChompIzSalsa.com</div></div>
  </div>
  <div class="contact-chip" style="left:782px">
    <svg width="22" height="22" viewBox="0 0 24 24" fill="none" stroke="#fff" stroke-width="1.5"><path d="M5 3h4l2 5-3 2a12 12 0 0 0 6 6l2-3 5 2v4a2 2 0 0 1-2 2A18 18 0 0 1 3 5a2 2 0 0 1 2-2z"/></svg>
    <div><div class="label">Call us</div><div class="value big">555.014.2273</div></div>
  </div>
  <div class="cart">
    <span>MY CART</span>
    <svg width="24" height="22" viewBox="0 0 24 22" fill="#fff"><path d="M1 2h4l3 11h12l3-8H7" fill="none" stroke="#fff" stroke-width="2"/><circle cx="9" cy="18" r="2"/><circle cx="19" cy="18" r="2"/></svg>
    <span class="count">0</span>
  </div>

  <nav class="main-nav">
    <a href="#" class="current" style="left:468px">HOME</a>
    <a href="#" style="left:553px">ABOUT US</a>
    <a href="#" style="left:672px">RECIPES</a>
    <a href="#" style="left:780px">BUY NOW</a>
    <a href="#" style="left:889px">EVENTS</a>
    <a href="#" style="left:984px">CONTACT US</a>
  </nav>
</header>

<section class="hero">
  <div class="abs hero-jar" role="img" aria-label="Jar of mild salsa in front of a bowl of fresh salsa and chips"></div>
  <div class="abs hero-title">RECIPE FOR<br>DOUBLE DIPPIN</div>
  <p class="abs hero-sub">Lorem Ipsum is simply dummy text of the printing and typesetting.</p>
  <a href="#" class="btn">BUY NOW</a>
</section>

<section class="welcome">
  <div class="abs kicker">Welcome to</div>
  <h1 class="heading">ChompIz Salsa</h1>
  <div class="rule"></div>
  <p class="abs lead">Lorem Ipsum is simply dummy text of the printing and typesetting.</p>
  <p class="abs body">There are many variations of passages of Lor em Ipsum available, but the majority have suffered alteration in some form, by injected humour, or randomised words which don't look even slightly believable. If you are going to use a passage of Lorem Ipsum, you need to be sure there isn't anything embarrassing hidden in the middle of text.</p>
  <a href="#" class="btn">READ MORE</a>
  <div class="abs welcome-photo" role="img" aria-label="Salsa jar on a plate between two soft tacos"></div>
  <div class="abs deco-hat" role="img" aria-label="Sombrero decoration"></div>
</section>

<section class="flavours">
  <div class="abs flavours-photo" role="img" aria-label="Three salsa jars: mild, medium and hot, against a brick wall"></div>
  <h2 class="heading">Flavours</h2>
  <div class="rule"></div>
  <div class="abs flavour-name" style="left:304px">MILD</div>
  <div class="abs flavour-name" style="left:608px">MEDIUM</div>
  <div class="abs flavour-name" style="left:900px">HOT</div>
  <a href="#" class="btn">BUY NOW</a>
  <div class="abs deco-chili" style="left:30px;top:642px" role="img" aria-label="Red chili peppers decoration"></div>
</section>

<section class="events">
  <h2 class="heading">Latest Events</h2>
  <div class="rule"></div>

  <article class="event-card" style="left:132px">
    <div class="photo" role="img" aria-label="Stacked salsa jars"></div>
    <span class="date">SUN, 6 JUN</span>
    <h3>Sip &amp; Shop</h3>
    <p>Chomp-iZ Salsa – 2250 W Maple Rd, Fairview, KS 66100-4120, United States</p>
    <a href="#" class="btn">READ MORE</a>
  </article>

  <article class="event-card" style="left:451px">
    <div class="photo" role="img" aria-label="Market stall with salsa jars on a striped tablecloth" style="background:linear-gradient(180deg,#8aa4c0,#5a5a55 50%,#c23a3a)"></div>
    <span class="date">SUN, 30 MAY</span>
    <h3>Route 9 Farmers Market</h3>
    <p>Chomp-iZ Salsa – 875 Route 9, Cedar Bluff, MO 64190, United States</p>
    <a href="#" class="btn">READ MORE</a>
  </article>

  <article class="event-card" style="left:769px">
    <div class="photo" role="img" aria-label="Three salsa jars in a row" style="background:linear-gradient(180deg,#6b4a3e,#3a3a3a 55%,#6e7478)"></div>
    <span class="date">SUN, 30 MAY</span>
    <h3>Route 9 Farmers Market</h3>
    <p>Chomp-iZ Salsa – 875 Route 9, Cedar Bluff, MO 64190, United States</p>
    <a href="#" class="btn">READ MORE</a>
  </article>
</section>

<section class="product">
  <h2 class="heading">Our Product</h2>
  <div class="rule"></div>
  <div class="abs product-card">
    <div class="abs product-jar" role="img" aria-label="Jar of mild salsa"></div>
    <div class="abs product-divider"></div>
    <h3>SALSA</h3>
    <p class="abs desc">There are many variations of passages of Lor em Ipsum available, but the majority have suffered alteration in some form, by injected humour</p>
    <div class="abs price">$50.00</div>
    <ul class="abs features">
      <li><svg width="10" height="8" viewBox="0 0 10 8"><path d="M1 4l3 3 5-6" fill="none" stroke="#f5b416" stroke-width="2"/></svg>There are many variations</li>
      <li><svg width="10" height="8" viewBox="0 0 10 8"><path d="M1 4l3 3 5-6" fill="none" stroke="#f5b416" stroke-width="2"/></svg>There are many variations</li>
      <li><svg width="10" height="8" viewBox="0 0 10 8"><path d="M1 4l3 3 5-6" fill="none" stroke="#f5b416" stroke-width="2"/></svg>It is a long established</li>
      <li><svg width="10" height="8" viewBox="0 0 10 8"><path d="M1 4l3 3 5-6" fill="none" stroke="#f5b416" stroke-width="2"/></svg>It is a long established</li>
      <li><svg width="10" height="8" viewBox="0 0 10 8"><path d="M1 4l3 3 5-6" fill="none" stroke="#f5b416" stroke-width="2"/></svg>Lorem Ipsum is simply</li>
      <li><svg width="10" height="8" viewBox="0 0 10 8"><path d="M1 4l3 3 5-6" fill="none" stroke="#f5b416" stroke-width="2"/></svg>Lorem Ipsum is simply</li>
    </ul>
    <a href="#" class="btn">BUY NOW</a>
  </div>
  <div class="abs deco-chili" style="left:964px;top:465px" role="img" aria-label="Red chili peppers decoration"></div>
</section>

<footer class="site-footer">
  <div class="abs footer-brand">Chomp-iZ Salsa</div>

  <div class="abs footer-title" style="left:479px">MENU</div>
  <ul class="abs footer-menu">
    <li>HOME</li><li>ABOUT US</li><li>RECIPES</li><li>BUY NOW</li><li>EVENTS</li><li>CONTACT US</li>
  </ul>

  <div class="abs footer-title" style="left:670px">CONTACT US</div>
  <div class="abs footer-item" style="left:668px;top:102px">
    <span class="dot"><svg width="10" height="13" viewBox="0 0 10 13"><path d="M5 0a5 5 0 0 1 5 5c0 4-5 8-5 8S0 9 0 5a5 5 0 0 1 5-5z" fill="#000"/><circle cx="5" cy="5" r="1.8" fill="#fff"/></svg></span>
    <div>4820 Juniper Avenue<br>Del Arbo, CA 91990</div>
  </div>
  <div class="abs footer-item" style="left:668px;top:153px">
    <span class="dot"><svg width="12" height="12" viewBox="0 0 24 24"><path d="M5 3h4l2 5-3 2a12 12 0 0 0 6 6l2-3 5 2v4a2 2 0 0 1-2 2A18 18 0 0 1 3 5a2 2 0 0 1 2-2z" fill="#000"/></svg></span>
    <div>Call Us<br>555.014.2273</div>
  </div>
  <div class="abs footer-item" style="left:668px;top:205px">
    <span class="dot"><svg width="12" height="9" viewBox="0 0 22 16"><rect x="1" y="1" width="20" height="14" fill="#000"/><path d="M1 1l10 8 10-8" fill="none" stroke="#fff" stroke-width="2"/></svg></span>
    <div>E mail Us<br>info@ChompIzSalsa.com</div>
  </div>

  <div class="abs footer-title" style="left:962px">FOLLOW US</div>
  <div class="abs footer-item" style="left:960px;top:102px"><span class="dot"></span><div>Like us on<br>FRIENDBOOK</div></div>
  <div class="abs footer-item" style="left:960px;top:153px"><span class="dot"></span><div>Follow us on<br>CHIRPER</div></div>
  <div class="abs footer-item" style="left:960px;top:205px"><span class="dot"></span><div>Follow us on<br>WORKLINK</div></div>

  <div class="abs footer-line"></div>
  <div class="abs copyright">Copyright © 2021 All Rights Reserved</div>
</footer>

</body>
</html>
```